Veluxa Bone & Motion Business Card

Need a business card using the logo provided. I want brand side of the card to be grey with the logo in the center of the card in white.

On the other side I leave to the designers

Target Market(s)

Personal Injury Attorneys

Industry/Entity Type

Medical

Contact Information for Business Card

Name, CEO. Cell Phone, (Hialeah, Address, Phone) (Homestead, Address, Phone) (Tallahassee, Address, Phone)

Colors

Designer to choose only greyscale colors for use in the design.

Requirements
Must have
• Logo by itself on one side

```html
<!DOCTYPE html>
<html lang="en">
<head>
<meta charset="utf-8">
<title>Veluxa Bone &amp; Motion – Business Card</title>
<link href="https://fonts.googleapis.com/css2?family=Lato:wght@700&family=Source+Sans+3:wght@400;700&display=swap" rel="stylesheet">
<style>
  :root {
    --backdrop: #e4e5e6;
    --brand-grey: #8ea7b0;
    --card-white: #f4f5f6;
    --ink: #2f3336;
    --logo-white: #f2f4f5;
  }
  * { margin: 0; padding: 0; box-sizing: border-box; }
  html, body { width: 1200px; height: 1200px; overflow: hidden; }
  body {
    position: relative;
    background: var(--backdrop);
    font-family: "Source Sans 3", Arial, sans-serif;
    color: var(--ink);
  }
  .card {
    position: absolute;
    left: 264px;
    width: 681px;
    height: 390px;
    border-radius: 36px;
  }
  .card--brand { top: 165px; background: var(--brand-grey); }
  .card--contact { top: 654px; background: var(--card-white); }

  .wordmark {
    position: absolute;
    font-family: "Lato", Arial, sans-serif;
    font-weight: 700;
    text-transform: uppercase;
    line-height: 1;
    white-space: nowrap;
  }
  .wordmark span { display: block; }
  .wordmark--center {
    left: 0; right: 0; top: 136px;
    text-align: center;
    color: var(--logo-white);
  }
  .wordmark--center .wordmark__main { font-size: 78px; letter-spacing: 10px; padding-left: 10px; }
  .wordmark--center .wordmark__sub { font-size: 36px; letter-spacing: 5px; padding-left: 5px; margin-top: 12px; }
  .wordmark--corner {
    right: 58px; top: 60px;
    text-align: right;
    color: var(--brand-grey);
  }
  .wordmark--corner .wordmark__main { font-size: 54px; letter-spacing: 7px; margin-right: -7px; }
  .wordmark--corner .wordmark__sub { font-size: 26px; letter-spacing: 4px; margin-right: -4px; margin-top: 9px; }

  .locations {
    position: absolute;
    left: 57px; top: 94px;
    font-size: 15.5px;
    line-height: 20px;
  }
  .location__phone { display: flex; align-items: center; gap: 6px; }
  .location__phone svg { width: 12px; height: 12px; }
  .divider {
    width: 28px; height: 3px;
    background: var(--brand-grey);
    margin: 19px 0 19px;
  }
  .holder {
    position: absolute;
    right: 58px; top: 272px;
    text-align: right;
    font-size: 15.5px;
    line-height: 21px;
  }
  .holder__name { font-weight: 700; font-size: 20px; color: var(--brand-grey); }
  .holder__cell { font-weight: 700; display: flex; justify-content: flex-end; align-items: center; gap: 8px; }
  .holder__cell svg { width: 10px; height: 17px; }
</style>
</head>
<body>
  <section class="card card--brand">
    <div class="wordmark wordmark--center">
      <span class="wordmark__main">Veluxa</span>
      <span class="wordmark__sub">Bone &amp; Motion</span>
    </div>
  </section>

  <section class="card card--contact">
    <div class="locations">
      <div class="location">
        <div class="location__phone"><svg viewBox="0 0 12 12"><path d="M3 1 L5 3.5 L4 5 Q5 7 7 8 L8.5 7 L11 9 L9.5 11 Q5 11 2 7 Q1 4 1 2.5 Z" fill="#8ea7b0"/></svg>555-210-0141</div>
        <div>412 W. Gaines Street</div>
        <div>Marlow Bay, FL 3241</div>
      </div>
      <div class="divider"></div>
      <div class="location">
        <div class="location__phone"><svg viewBox="0 0 12 12"><path d="M3 1 L5 3.5 L4 5 Q5 7 7 8 L8.5 7 L11 9 L9.5 11 Q5 11 2 7 Q1 4 1 2.5 Z" fill="#8ea7b0"/></svg>555-210-0142</div>
        <div>27 Krome Plaza</div>
        <div>Cedar Hollow, FL 3312</div>
      </div>
      <div class="divider"></div>
      <div class="location">
        <div class="location__phone"><svg viewBox="0 0 12 12"><path d="M3 1 L5 3.5 L4 5 Q5 7 7 8 L8.5 7 L11 9 L9.5 11 Q5 11 2 7 Q1 4 1 2.5 Z" fill="#8ea7b0"/></svg>555-210-0143</div>
        <div>880 Ember Avenue</div>
        <div>Palmira, Florida 3301</div>
      </div>
    </div>

    <div class="wordmark wordmark--corner">
      <span class="wordmark__main">Veluxa</span>
      <span class="wordmark__sub">Bone &amp; Motion</span>
    </div>

    <div class="holder">
      <div class="holder__name">Renata Calloway</div>
      <div>Chief Executive Officer</div>
      <div class="holder__cell">+1 555-210-0199 <svg viewBox="0 0 10 17"><rect x="0.75" y="0.75" width="8.5" height="15.5" rx="1.5" fill="none" stroke="#8ea7b0" stroke-width="1.5"/><line x1="3.5" y1="13.5" x2="6.5" y2="13.5" stroke="#8ea7b0" stroke-width="1.2"/></svg></div>
    </div>
  </section>
</body>
</html>
```